Postcard Design

I am looking for a hand out for festivals
This is an gift and antique/home décor shop
Located in a renovated barn... The gifts are timeless and the home décor pieces are the unusual... Looing for something to impress, look no more

The piece should include pictures of product and the store
A map to our place... 4126 Maple Hollow Lane Bryan Texas
Address, Hours of Operation: Wed- Saturday 10-7

Copper Fern Keepsakes takes pride in offering the best in timeless gifs and home décor.. We are dedicated to putting the "WOW" back in gift giving and home decorating.

The story began with a husband who collected antiques for years, add in a renovated barn for the ambiance and a wife who loves to shop with an eye toward elegance,

The Result : Copper Fern Keepsakes.

We are committed to offering the Unique....

At Copper Fern Keepsakes, we provide customers a wide selection of Gifts and Collectibles at the most affordable prices.

Having a hard time finding that unique gift, We Have It Here!!!

Timeless + Classy = Gifts for all Seasons

Visit us today at our renovated Barn in Bryan, TX to see our unique collection of Timeless Gifts and Collectibles
Updates

you guys have made this a very hard choice... While I have choosen a "post card" design... the initial desire was a handout at a festival.. I will need a separate one for a mailer.

Target Market(s)

We are near a college town.. Looking to target individuals interested in the unique

Industry/Entity Type

Shop

Requirements
Must have
• A inviting card that will create curiosity and a desire to go on a treasure hunt. The card must us a cross section of the pictures

The goal is a desire to seek out this store

```html
<!DOCTYPE html>
<html lang="en">
<head>
<meta charset="utf-8">
<title>Copper Fern Keepsakes – Festival Postcard</title>
<link href="https://fonts.googleapis.com/css2?family=Source+Sans+3:wght@400;600&display=swap" rel="stylesheet">
<style>
  :root {
    --backdrop: #e2e2e2;
    --paper: #ffffff;
    --maroon: #5c0a25;
    --map-tone: #a36b7c;
    --on-maroon: #ffffff;
  }
  html, body {
    margin: 0;
    padding: 0;
    width: 1200px;
    height: 900px;
    overflow: hidden;
    background: var(--backdrop);
    font-family: "Source Sans 3", "Source Sans Pro", sans-serif;
  }
  .postcard {
    position: absolute;
    left: 251px;
    top: 148px;
    width: 728px;
    height: 564px;
    display: flex;
    box-shadow: 3px 4px 6px rgba(0,0,0,0.35);
  }
  .info-side {
    position: relative;
    width: 359px;
    height: 100%;
    background: var(--paper);
    color: var(--maroon);
  }
  .story-side {
    position: relative;
    width: 369px;
    height: 100%;
    background: var(--maroon);
    color: var(--on-maroon);
    text-align: center;
  }
  .shop-mark {
    position: absolute;
    left: 164px;
    top: 40px;
    width: 30px;
    height: 30px;
    border-radius: 50%;
    background: var(--maroon);
  }
  .shop-name {
    position: absolute;
    top: 78px;
    left: 0;
    width: 359px;
    margin: 0;
    font-size: 30px;
    font-weight: 400;
    line-height: 1.1;
    text-align: center;
  }
  .address {
    position: absolute;
    top: 155px;
    left: 0;
    width: 359px;
    margin: 0;
    text-align: center;
    font-size: 14px;
    line-height: 18px;
  }
  .location-map {
    position: absolute;
    left: 22px;
    top: 192px;
    width: 314px;
    height: 232px;
    background: var(--map-tone);
  }
  .hours {
    position: absolute;
    left: 23px;
    top: 432px;
    margin: 0;
  }
  .hours-label {
    display: block;
    font-size: 11px;
    font-weight: 600;
    line-height: 13px;
  }
  .hours-time {
    display: block;
    font-size: 16px;
    line-height: 18px;
  }
  .story-side p { position: absolute; margin: 0; }
  .lead { left: 22px; width: 325px; top: 60px; font-size: 17.5px; font-weight: 600; line-height: 21.5px; }
  .origin { left: 27px; width: 315px; top: 181px; font-size: 14px; line-height: 17.5px; }
  .promise { left: 22px; width: 325px; top: 265px; font-size: 14px; line-height: 17.5px; }
  .selection { left: 22px; width: 325px; top: 296px; font-size: 17px; line-height: 21.5px; }
  .invite { left: 24px; width: 321px; top: 375px; font-size: 14px; line-height: 17.5px; }
  .tagline { left: 22px; width: 325px; top: 424px; font-size: 17px; line-height: 21px; }
  .visit { left: 22px; width: 325px; top: 458px; font-size: 12.5px; line-height: 16px; }
</style>
</head>
<body>
  <article class="postcard">
    <section class="info-side">
      <span class="shop-mark" aria-hidden="true"></span>
      <h1 class="shop-name">Copper Fern Keepsakes</h1>
      <p class="address">4126 Maple Hollow Lane Bryan Texas</p>
      <div class="location-map" role="img" aria-label="Map showing the shop's location near the highway and the university campus in Bryan, Texas"></div>
      <p class="hours">
        <span class="hours-label">Hours of Operation</span>
        <span class="hours-time">Wed- Saturday 10-7</span>
      </p>
    </section>
    <section class="story-side">
      <p class="lead">Copper Fern Keepsakes takes pride in offering the best in timeless gifs and home décor.. We are dedicated to putting the "WOW" back in gift giving and home decorating.</p>
      <p class="origin">The story began with a husband who collected antiques for years, add in a renovated barn for the ambiance and a wife who loves to shop with an eye toward elegance,</p>
      <p class="promise">We are committed to offering the Unique....</p>
      <p class="selection">At Copper Fern Keepsakes, we provide customers a wide selection of Gifts and Collectibles at the most affordable prices.</p>
      <p class="invite">Having a hard time finding that unique gift, We Have It Here!!!</p>
      <p class="tagline">Timeless + Classy = Gifts for all Seasons</p>
      <p class="visit">Visit us today at our renovated Barn in Bryan, TX to see our unique collection of Timeless Gifts and Collectibles</p>
    </section>
  </article>
</body>
</html>
```